Family business needs stationery redesign with new logo

Family owned company, established in 1987 wanting a brand 'refresh'. We are an electrical, refrigeration and construction company based in the Barkly Region Northern Territory, Australia. We have a new logo we would like to use which is uploaded along with our current letterhead and email signature. We are also dropping the word 'contractors' so please do not include this on any designs. Please note also, the 'orange' color used in our logo and designs should be Northern Territory red ochre which is as follows:

RGB (Hex): #C75B12
PantoneĀ® 159 C
CMYK: 1 / 74 / 100 / 7

We are needing our stationery redesigned using our new logo. Please include letterheads, business cards, envelopes, and email signatures.

We currently use our business letterheads for quotations, invoices, letters, HR matters, and internal memos.

We also need a separate simplified letterhead for internal paperwork such as employee leave forms, meeting agendas, and meeting minutes etc.

Reason: Needing more submissions of full package designs. We are wanting all our stationery, including business cards, letterheads, email signatures, envelopes, etc to be cohesive. We also require ALL the information, as supplied on our template letterhead, to be included on the new letterhead designs. including electrical license no.etc Thank you, R&W

Reason: needing more time as work has got in the way of looking over designs. A lot of designs not meeting the brief/criteria.

Industry/Entity Type

Business

Colors
0355a3
f37122

Requirements
Must have
• The 'orange' color used in the designs should be Northern Territory red ochre which is as follows:
• RGB (Hex): #C75B12
• PantoneĀ® 159 C
• CMYK: 1 / 74 / 100 / 7
• ***MUST INCLUDE ALL INFORMATION THAT IS ON OUR CURRENT LETTERHEAD***
Should not have
• Please do not include the word 'contractors'

```html
<!DOCTYPE html>
<html lang="en">
<head>
<meta charset="utf-8">
<title>R&amp;W Stationery Set</title>
<link href="https://fonts.googleapis.com/css2?family=Arimo:wght@400;700&family=Tinos&display=swap" rel="stylesheet">
<style>
:root{
  --navy:#1b3170;
  --ochre:#c75b12;
  --paper:#ffffff;
  --backdrop:#e9e9ea;
  --ink:#333333;
}
*{margin:0;padding:0;box-sizing:border-box}
html,body{width:1200px;height:938px;overflow:hidden;background:var(--backdrop)}
body{position:relative;font-family:'Arimo',sans-serif;color:var(--ink)}
.sheet{position:absolute;background:var(--paper);overflow:hidden}
.footer-band{position:absolute;left:0;bottom:0;width:100%;
  background:linear-gradient(180deg,rgba(199,91,18,0) 0%,rgba(199,91,18,.28) 30%,rgba(27,49,112,.75) 62%,var(--navy) 100%)}
.brand{position:absolute;display:flex;align-items:center;gap:8px}
.brand-mark{display:flex;align-items:center;gap:5px;font-family:'Arimo',sans-serif;font-weight:700;color:var(--navy);line-height:1}
.brand-dot{border-radius:50%;background:var(--ochre);display:inline-block}
.brand-services{font-family:'Tinos',serif;color:var(--navy);line-height:1.2}

/* letterhead */
.letterhead{left:184px;top:68px;width:386px;height:544px}
.letterhead .brand{left:18px;top:24px}
.letterhead .brand-mark{font-size:24px}
.letterhead .brand-dot{width:8px;height:8px}
.letterhead .brand-services{font-size:8.5px}
.letterhead .footer-band{height:128px}
.contact{position:absolute;right:18px;top:24px;text-align:right;font-size:4.8px;line-height:10px;color:#222;letter-spacing:.2px}
.letter{position:absolute;left:37px;top:140px;width:296px;font-size:5.2px;line-height:8.2px;color:#444}
.letter p{margin-bottom:10px}
.letter .gap{margin-bottom:22px}
.letter strong{color:#222}
.signature{width:38px;height:22px;margin:6px 0 8px;background:linear-gradient(90deg,#777,#bbb);opacity:.5;border-radius:3px}

/* folder */
.folder{left:636px;top:42px;width:458px;height:574px}
.folder .brand{left:0;right:0;top:222px;flex-direction:column;gap:10px}
.folder .brand-mark{font-size:50px;gap:10px}
.folder .brand-dot{width:16px;height:16px}
.folder .brand-services{font-size:17px;text-align:center;line-height:1.1}
.folder .footer-band{height:152px}

/* business cards */
.card{width:176px;height:98px;border-radius:8px}
.card-front{left:46px;top:660px}
.card-back{left:46px;top:786px}
.card .brand-mark{font-size:14px;gap:3px}
.card .brand-dot{width:5px;height:5px}
.card .brand-services{font-size:5px}
.card-front .brand{left:6px;top:10px;gap:5px}
.card-front .footer-band{height:36px}
.card-back .brand{left:42px;top:38px;gap:5px}
.card-contact{position:absolute;left:10px;top:48px;font-size:3.4px;line-height:5px;color:#333}
.card-person{position:absolute;right:14px;top:48px;text-align:right;font-size:5px;line-height:5.5px;color:#222}
.card-person span{display:block;font-size:3px}

/* envelopes */
.envelope-front{left:266px;top:674px;width:431px;height:207px}
.envelope-front .brand{left:15px;top:20px;gap:10px}
.envelope-front .brand-mark{font-size:24px}
.envelope-front .brand-dot{width:8px;height:8px}
.envelope-front .brand-services{font-size:8px}
.envelope-front .footer-band{height:140px}
.envelope-back{left:737px;top:672px;width:432px;height:208px;border-radius:0 4px 0 0}
.envelope-flap{position:absolute;left:0;top:0;width:100%;height:72px;background:var(--navy);border-radius:0 0 34px 34px}
</style>
</head>
<body>

<section class="sheet letterhead">
  <div class="brand">
    <div class="brand-mark"><span class="brand-dot"></span>R&amp;W</div>
    <div class="brand-services">Electrical<br>Refrigeration<br>Building Services</div>
  </div>
  <div class="contact">
    14 Ochre Street<br>Tennant Creek NT<br>08 8962 0142<br>08 8962 0143<br>08 8962 0144<br>office@rwservices.au<br>www.rwservices.au
  </div>
  <div class="letter">
    <p>July 2, 2012</p>
    <p><strong>Dear CH,</strong><br>Ridge House, Elm St., Australia</p>
    <p>Thank you for the chance to quote on the electrical and refrigeration works at your site. Our team has reviewed the plans and will supply all labour, materials and testing needed to complete the job to current standards. Work can begin within two weeks of approval and will be carried out with as little disruption to your staff as possible. Full details of costs, timing and warranty terms are set out in the attached schedule for your review.</p>
    <p class="gap">Should you need any changes to the scope of works, please let us know and we will gladly revise the quote and send it back to you promptly.</p>
    <p>All of our electricians and technicians hold current licences and are trained in safe work practice on commercial and remote sites. We service the whole region and keep a full stock of parts so that repairs can be finished on the first visit wherever we can. Our office staff will confirm bookings by phone and email, and a written report is provided at the end of every job so you have a clear record of all work done.</p>
    <p style="margin-bottom:0">Best Regards,</p>
    <div class="signature" role="img" aria-label="Handwritten signature"></div>
    <p><strong>Daniel Hart</strong><br>Director<br><br>Ridge House, Elm St., Australia</p>
  </div>
  <div class="footer-band" role="img" aria-label="Curved navy and ochre decorative band"></div>
</section>

<section class="sheet folder">
  <div class="brand">
    <div class="brand-mark"><span class="brand-dot"></span>R&amp;W</div>
    <div class="brand-services">Electrical<br>Refrigeration<br>Building Services</div>
  </div>
  <div class="footer-band" role="img" aria-label="Curved navy and ochre decorative band"></div>
</section>

<section class="sheet card card-front">
  <div class="brand">
    <div class="brand-mark"><span class="brand-dot"></span>R&amp;W</div>
    <div class="brand-services">Electrical<br>Refrigeration<br>Building Services</div>
  </div>
  <div class="card-contact">08 8962 0142<br>08 8962 0143<br>08 8962 0144<br>office@rwservices.au</div>
  <div class="card-person">JORDAN PRICE<span>PRESIDENT</span></div>
  <div class="footer-band" role="img" aria-label="Curved navy and ochre decorative band"></div>
</section>

<section class="sheet card card-back">
  <div class="brand">
    <div class="brand-mark"><span class="brand-dot"></span>R&amp;W</div>
    <div class="brand-services">Electrical<br>Refrigeration<br>Building Services</div>
  </div>
</section>

<section class="sheet envelope-front">
  <div class="brand">
    <div class="brand-mark"><span class="brand-dot"></span>R&amp;W</div>
    <div class="brand-services">Electrical<br>Refrigeration<br>Building Services</div>
  </div>
  <div class="footer-band" role="img" aria-label="Curved navy and ochre decorative band"></div>
</section>

<section class="sheet envelope-back">
  <div class="envelope-flap"></div>
</section>

</body>
</html>
```